Lone Star Wetland Flora Stewardship Guild

We need to design the home page of this new website. We would like a fun website design for provides as a resource for members and information for potential members.
Please design so that we can see a portion of background on each side on the website.
I just need the final design files psd no coding needed.
Attached is their logo (colors are not 100% set in stone either so can mess with those as I did in the quick mockup attached)
Attached is a pdf newsletter they send out, you can get a feel for them and what they are about. The design is crappy and we are here to fix that going forward and we are starting with the website.
Here are some quick example websites (design style is open)
- I attached a quick mockup i did just for a content visual but by all means do what you want.
- http://www.brightpathleaders.example/
- http://www.civicunityhub.example/
- http://preview.webskinvault.example/show.php?cat=layouts&host=skinbazaar&temp=novaline
- http://www.meadowkeep.example/
- http://www.urbangleaners.example/
- http://www.projectcozyknit.example/
here are some of the other chapters website (pretty bad!)
and here are some of the others:
- http://www.dwrvcs.example/
- http://kwfg.example/
- http://www.blvcg.example/
Content Items that need to be included:
1. Logo
2. Menu - home, about, members, resources, events, membership, contact
3. Become a member - button or action
4. social links - chatterloop, workweave, clipstream
5. banner - that needs to explain their purpose "Promoting environmental stewardship through operations, research, education and outreach" (or this can be worked into the design)
6. Upcoming event (s)
7. Advertisement - members can place an ad on the website, this can be a placeholder for now
8. newsletter signup
9. advertise with us - this link can be in the footer
30-60 years of age, succesfull (household budgets of 120K+ men and women that live in texas.
Education

```html
<!DOCTYPE html>
<html lang="en">
<head>
<meta charset="utf-8">
<title>Lone Star Wetland Flora Stewardship Guild</title>
<link href="https://fonts.googleapis.com/css2?family=Carlito:wght@400;700&display=swap" rel="stylesheet">
<style>
:root{
  --brand-blue:#0b3f8f;
  --heading-blue:#123f8c;
  --accent-red:#d8434f;
  --text-dark:#333333;
  --text-muted:#8a8a8a;
  --panel-white:#ffffff;
  --newsletter-grey:#e7e7e7;
}
*{box-sizing:border-box;margin:0;padding:0}
html,body{width:1200px;height:1181px;overflow:hidden}
body{position:relative;font-family:"Carlito",Calibri,sans-serif;color:var(--text-dark);background:#fff}
.top-rule{position:absolute;left:0;top:0;width:1200px;height:3px;background:var(--accent-red)}
.site-header{position:absolute;left:0;top:3px;width:1200px;height:119px;background:#fff}
.brand{position:absolute;left:124px;top:30px;display:flex;align-items:center;gap:10px}
.brand-mark{width:34px;height:34px;background:var(--accent-red)}
.brand-name{font-size:17px;font-weight:700;color:var(--brand-blue);width:210px;line-height:1.15}
.social{position:absolute;top:51px;left:778px;display:flex;gap:10px}
.social a{width:36px;height:34px;border-radius:6px;background:var(--brand-blue);color:#fff;font-size:8px;display:flex;align-items:center;justify-content:center;text-decoration:none}
.social a.clip{background:var(--accent-red)}
.btn-member{position:absolute;left:914px;top:51px;width:164px;height:31px;background:var(--accent-red);color:#fff;font-size:16px;display:flex;align-items:center;justify-content:center;border-radius:2px;box-shadow:1px 2px 3px rgba(0,0,0,.3);text-decoration:none}
.main-nav{position:absolute;left:0;top:122px;width:1200px;height:38px;background:var(--brand-blue)}
.main-nav a{position:absolute;top:0;line-height:38px;color:#fff;font-size:15px;text-decoration:none;transform:translateX(-50%)}
.backdrop{position:absolute;left:0;top:160px;width:1200px;height:1021px;background:linear-gradient(180deg,#bcd3e6 0%,#9fb9a8 25%,#6c8fa6 40%,#8b6a4e 62%,#b4a466 80%,#a9b56b 100%)}
.slider{position:absolute;left:120px;top:184px;width:960px;height:372px;border:4px solid #fff;background:linear-gradient(180deg,#6f9e96 0%,#4f8470 40%,#3f6b4c 70%,#2f4a35 100%)}
.slider-caption{position:absolute;left:26px;top:204px;width:462px;height:94px;background:rgba(40,40,40,.55);border-left:3px solid var(--accent-red);padding:14px 0 0 14px;color:#fff;font-size:21px;line-height:33px}
.slider-arrows{position:absolute;left:900px;top:330px}
.content{position:absolute;left:120px;top:574px;width:958px;height:522px;background:var(--panel-white)}
.section-title{position:absolute;font-size:24px;color:var(--heading-blue);font-weight:400}
.about-text{position:absolute;left:15px;top:62px;width:520px;font-size:12px;line-height:22.5px}
.about-text p+p{margin-top:22.5px}
.event{position:absolute;width:290px;height:72px}
.event .thumb{position:absolute;left:0;top:0;width:72px;height:72px}
.event .info{position:absolute;left:85px;top:-2px;font-size:12px;line-height:22.5px;width:205px}
.event .more{color:var(--accent-red);text-decoration:none}
.ad-space{position:absolute;left:650px;top:21px;width:300px;height:279px;background:linear-gradient(180deg,#9fb2a4 0%,#7f8a70 50%,#5e5a48 100%)}
.ad-caption{position:absolute;left:4px;bottom:6px;width:287px;background:rgba(40,40,40,.55);color:#fff;font-size:27px;line-height:28px;padding:2px 4px}
.newsletter{position:absolute;left:650px;top:329px;width:300px;height:159px;background:var(--newsletter-grey)}
.newsletter h3{position:absolute;left:16px;top:16px;font-size:18px;font-weight:400;color:var(--heading-blue);letter-spacing:.3px}
.newsletter p{position:absolute;left:16px;top:48px;width:200px;font-size:12px;line-height:22px;color:var(--text-muted)}
.newsletter .divider{position:absolute;left:234px;top:10px;width:1px;height:86px;background:#c6c6c6}
.newsletter svg{position:absolute;left:245px;top:38px}
.newsletter .field{position:absolute;left:16px;top:110px;width:214px;height:35px;background:#fff;border:0}
.newsletter .go{position:absolute;left:230px;top:110px;width:58px;height:35px;background:var(--accent-red);color:#fff;font-size:19px;display:flex;align-items:center;justify-content:center}
.site-footer{position:absolute;left:120px;top:1110px;width:958px;height:34px;background:#fff;font-size:12px;display:flex;align-items:center;justify-content:space-between;padding:0 13px 0 15px}
.site-footer .advertise{color:var(--accent-red);font-size:15px;font-weight:700;text-decoration:underline}
</style>
</head>
<body>
<div class="top-rule"></div>
<header class="site-header">
  <div class="brand"><span class="brand-mark"></span><span class="brand-name">Lone Star Wetland Flora Stewardship Guild</span></div>
  <nav class="social" aria-label="Social links">
    <a class="clip" href="#">clipstream</a>
    <a href="#">chatterloop</a>
    <a href="#">workweave</a>
  </nav>
  <a class="btn-member" href="#">BECOME A MEMBER</a>
</header>
<nav class="main-nav" aria-label="Main">
  <a href="#" style="left:163px">HOME</a>
  <a href="#" style="left:286px">ABOUT</a>
  <a href="#" style="left:423px">MEMBERS</a>
  <a href="#" style="left:571px">RESOURCES</a>
  <a href="#" style="left:714px">EVENTS</a>
  <a href="#" style="left:864px">MEMBERSHIP</a>
  <a href="#" style="left:1020px">CONTACT</a>
</nav>
<div class="backdrop" role="img" aria-label="Background photo of a lake covered with lily pads under a blue sky"></div>
<section class="slider" role="img" aria-label="Banner photo of water lilies and reeds on a pond">
  <div class="slider-caption">Promoting environmental stewardship through<br>Operations, Research, Education and Outreach</div>
  <svg class="slider-arrows" width="36" height="22" viewBox="0 0 36 22"><path d="M12 2 4 11l8 9M24 2l8 9-8 9" fill="none" stroke="#fff" stroke-width="4"/></svg>
</section>
<main class="content">
  <h2 class="section-title" style="left:15px;top:18px">About Us</h2>
  <div class="about-text">
    <p>Proin gravida nibh vel velit auctor aliquet. Aenean sollicitudin, lorem quis bibendum auctor, nisi elit consequat ipsum, nec sagittis sem nibh id elit. Duis sed odio sit amet nibh vulputate cursus a sit amet mauris. Morbi accumsan ipsum velit. Nam nec tellus a odio tincidunt auctor a ornare odio. Sed non&nbsp; mauris vitae erat consequat auctor eu in elit.</p>
    <p>Class aptent taciti sociosqu ad litora torquent per conubia nostra, per inceptos himenaeos. Mauris in erat justo. Nullam ac urna eu felis dapibus condimentum.</p>
  </div>
  <h2 class="section-title" style="left:14px;top:246px">Upcoming event</h2>
  <div class="event" style="left:15px;top:312px"><div class="thumb" role="img" aria-label="Event photo of marsh grasses" style="background:linear-gradient(160deg,#8fbf5a,#3d6b2c)"></div><div class="info">Aenean sollicitudin, lorem quis biben dum auctor nisi elit aipsum nec.<br><a class="more" href="#">Read More</a></div></div>
  <div class="event" style="left:318px;top:311px"><div class="thumb" role="img" aria-label="Event photo of a lily pond with trees" style="background:linear-gradient(180deg,#a8c8e8,#6f9a4a 55%,#b8a24a)"></div><div class="info">Aenean sollicitudin, lorem quis biben dum auctor nisi elit aipsum nec.<br><a class="more" href="#">Read More</a></div></div>
  <div class="event" style="left:15px;top:416px"><div class="thumb" role="img" aria-label="Event photo of a purple water lily bloom" style="background:linear-gradient(150deg,#7a3ea0,#c77bd0 50%,#e2b64a)"></div><div class="info">Aenean sollicitudin, lorem quis biben dum auctor nisi elit aipsum nec.<br><a class="more" href="#">Read More</a></div></div>
  <div class="event" style="left:318px;top:415px"><div class="thumb" role="img" aria-label="Event photo of a pond with floating plants" style="background:linear-gradient(160deg,#5a7a5a,#2f4a4a 60%,#6a5a7a)"></div><div class="info">Aenean sollicitudin, lorem quis biben dum auctor nisi elit aipsum nec.<br><a class="more" href="#">Read More</a></div></div>
  <aside class="ad-space" role="img" aria-label="Member advertisement photo of two field workers on an airboat">
    <div class="ad-caption">Freshwater Fish | Plant Management</div>
  </aside>
  <form class="newsletter">
    <h3>Subscribe Our Newsletter</h3>
    <p>sit amet mauris. Morbi accumsan ipsum velit. Nam nec tellus a odio tincidunt</p>
    <span class="divider"></span>
    <svg width="42" height="32" viewBox="0 0 42 32"><rect x="2" y="2" width="38" height="28" fill="none" stroke="var(--brand-blue)" stroke-width="3"/><path d="M2 2l19 16L40 2M2 30l14-13M40 30 26 17" fill="none" stroke="var(--brand-blue)" stroke-width="3"/></svg>
    <input class="field" type="email" aria-label="Email address">
    <span class="go">GO</span>
  </form>
</main>
<footer class="site-footer">
  <span>copyright © 2014 | Privacy Policy</span>
  <a class="advertise" href="#">Advertise with us</a>
</footer>
</body>
</html>
```